Quorva - corporate Business Card

We need a good look and innovative business card for a new start up company based in Los Angeles called "Quorva". We are in a payment business, including payment card, app, and ewallet. We are expert in online payment and Card not present (CNP) transaction.
We need an innovative, modern business card.

Our logo font is Aero Matics

Target Market(s)

Startup - Bank - Online Payment - Card Manufacturing

Industry/Entity Type

Startup

Contact Information for Business Card

phone: 555 014 7396 - Address: 4172 Marlowe blvd, Tarvin Heights, CA 90299

Requirements
Must have
• Message: innovative, professional, expert, high tech, trust, online payment expert, security
Nice to have
• no comment
Should not have
• no Comment

```html
<!DOCTYPE html>
<html lang="en">
<head>
<meta charset="utf-8">
<title>Quorva – Business Card</title>
<link rel="stylesheet" href="https://fonts.googleapis.com/css2?family=Open+Sans:wght@400;600;700&display=swap">
<style>
  :root {
    --backdrop: #1d1d1d;
    --front-grey: #5b5b5b;
    --front-halo: rgba(255,255,255,0.09);
    --paper: #ffffff;
    --brand-red: #b5202e;
    --ink: #555555;
    --ink-dark: #333333;
    --divider: #c9c9c9;
  }
  * { margin: 0; padding: 0; box-sizing: border-box; }
  html, body { width: 1200px; height: 1000px; overflow: hidden; }
  body {
    background: var(--backdrop);
    font-family: "Open Sans", Arial, sans-serif;
    position: relative;
  }
  .card {
    position: absolute;
    left: 290px;
    width: 620px;
    height: 350px;
    border-radius: 18px;
    overflow: hidden;
  }
  .card-front { top: 100px; background: var(--front-grey); }
  .card-back { top: 540px; background: var(--paper); }

  .front-halo {
    position: absolute;
    left: 180px; top: 45px;
    width: 260px; height: 260px;
    border-radius: 50%;
    background: var(--front-halo);
  }
  .front-wordmark {
    position: absolute;
    left: 0; right: 0; top: 118px;
    text-align: center;
    color: #ffffff;
    font-weight: 700;
    font-size: 96px;
    line-height: 1;
    letter-spacing: 2px;
    text-transform: lowercase;
  }

  .brand-disc {
    position: absolute;
    left: 80px; top: 92px;
    width: 166px; height: 166px;
    border-radius: 50%;
    background: var(--brand-red);
    display: flex; align-items: center; justify-content: center;
    color: #ffffff;
    font-weight: 700;
    font-size: 30px;
    letter-spacing: 1px;
  }
  .back-divider {
    position: absolute;
    left: 300px; top: 120px;
    width: 1px; height: 140px;
    background: var(--divider);
  }
  .contact-block {
    position: absolute;
    left: 330px; top: 118px;
  }
  .person-name { color: var(--brand-red); font-weight: 700; font-size: 19px; line-height: 1.1; }
  .person-role { color: var(--ink-dark); font-weight: 600; font-size: 12px; margin-top: 3px; }
  .address { color: var(--ink); font-size: 13px; line-height: 1.3; margin-top: 6px; }
  .contact-list { list-style: none; margin-top: 12px; }
  .contact-list li {
    display: flex; align-items: center; gap: 10px;
    color: var(--ink); font-size: 13px; line-height: 1; margin-bottom: 5px;
  }
  .contact-icon { width: 14px; height: 14px; flex: none; }
  .accent { color: var(--brand-red); }
</style>
</head>
<body>
  <section class="card card-front" aria-label="Card front">
    <div class="front-halo"></div>
    <div class="front-wordmark">quorva</div>
  </section>

  <section class="card card-back" aria-label="Card back">
    <div class="brand-disc">Quorva</div>
    <div class="back-divider"></div>
    <div class="contact-block">
      <p class="person-name">Lena Hartwell</p>
      <p class="person-role">Ceo &amp; Founder</p>
      <p class="address">4172 Marlowe blvd,<br>Tarvin Heights, CA 90299</p>
      <ul class="contact-list">
        <li>
          <svg class="contact-icon" viewBox="0 0 14 14" aria-hidden="true">
            <circle cx="7" cy="7" r="7" fill="#b5202e"/>
            <path d="M4.3 3.6c.4-.3.8-.2 1 .2l.6 1.1c.2.3.1.6-.2.8l-.4.3c.4.9 1 1.5 1.9 1.9l.3-.4c.2-.3.5-.4.8-.2l1.1.6c.4.2.5.6.2 1l-.5.6c-.3.3-.8.4-1.2.2C6 9.3 4.7 8 4 6.2c-.2-.4-.1-.9.2-1.2z" fill="#fff"/>
          </svg>
          555 014 7396
        </li>
        <li>
          <svg class="contact-icon" viewBox="0 0 14 14" aria-hidden="true">
            <circle cx="7" cy="7" r="7" fill="#b5202e"/>
            <rect x="3.5" y="4.5" width="7" height="5" rx=".6" fill="#fff"/>
            <path d="M3.7 4.8L7 7.3l3.3-2.5" stroke="#b5202e" stroke-width=".8" fill="none"/>
          </svg>
          yourname@email.com
        </li>
        <li>
          <svg class="contact-icon" viewBox="0 0 14 14" aria-hidden="true">
            <circle cx="7" cy="7" r="7" fill="#b5202e"/>
            <circle cx="7" cy="7" r="3.6" stroke="#fff" stroke-width=".9" fill="none"/>
            <path d="M3.4 7h7.2M7 3.4c-1.6 2-1.6 5.2 0 7.2M7 3.4c1.6 2 1.6 5.2 0 7.2" stroke="#fff" stroke-width=".7" fill="none"/>
          </svg>
          <span>www.<span class="accent">websitename</span>.com</span>
        </li>
      </ul>
    </div>
  </section>
</body>
</html>
```